CREATE A 2 layout and logo ( servanilo )

I need to create 2 layout for my company being a homepage will be like and other client control panel and need to create the logo of the company, my company works with website hosting and sale of dedicated server and VPS cloud the company name and servanilo, I want the site to be very accessible and that is not too flashy

Target Market(s)

website hosting

Industry/Entity Type

It Company

Number of Pages Required

2 page

Font styles to use
Sans Serif

Requirements
Must have
• domain servanilo.example
Nice to have
• banners, login area, login webmail
Should not have
• no preference

```html
<!DOCTYPE html>
<html lang="en">
<head>
<meta charset="utf-8">
<title>servanilo — Cloud Hosting</title>
<link href="https://fonts.googleapis.com/css2?family=Signika:wght@300;400;600&family=Open+Sans:wght@400;600&display=swap" rel="stylesheet">
<style>
:root{
  --green:#36ae68;
  --green-dark:#2f9a5b;
  --ink:#262626;
  --ink-soft:#1f1f1f;
  --text:#333;
  --muted:#555;
  --mist:#e8ebec;
  --white:#fff;
}
*{margin:0;padding:0;box-sizing:border-box}
html,body{width:1200px;height:2550px;overflow:hidden}
body{font-family:"Open Sans",Arial,sans-serif;color:var(--text);background:var(--white);position:relative}
.heading{font-family:"Signika",Arial,sans-serif;font-weight:300}
a{color:inherit;text-decoration:none}

/* top bar */
.topbar{position:absolute;left:0;top:0;width:1200px;height:77px;background:var(--ink)}
.brand{position:absolute;left:97px;top:20px;font-family:"Signika",sans-serif;font-weight:600;font-size:29px;color:var(--white)}
.nav{position:absolute;left:474px;top:0;height:77px;display:flex;align-items:center;gap:30px;font-family:"Signika",sans-serif;font-weight:300;font-size:14px;color:#9a9a9a}
.nav .home{width:18px;height:16px}
.signup{position:absolute;left:923px;top:19px;width:83px;height:42px;background:var(--green);color:var(--white);font-family:"Signika",sans-serif;font-weight:300;font-size:14px;display:flex;align-items:center;justify-content:center}
.langs{position:absolute;left:1063px;top:36px;display:flex;gap:6px}
.langs span{width:11px;height:8px;display:block}

/* hero */
.hero{position:absolute;left:0;top:77px;width:1200px;height:543px;background:var(--green)}
.hero-title{position:absolute;left:97px;top:146px;font-family:"Signika",sans-serif;font-weight:600;font-size:56px;color:var(--white);text-shadow:0 3px 4px rgba(0,0,0,.25)}
.hero-sub{position:absolute;left:99px;top:230px;width:330px;font-size:13px;line-height:21px;color:var(--white)}
.hero-btn{position:absolute;left:99px;top:307px;width:212px;height:63px;background:var(--ink);color:var(--white);font-family:"Signika",sans-serif;font-weight:600;font-size:18px;letter-spacing:.5px;display:flex;align-items:center;justify-content:center;box-shadow:0 3px 0 rgba(0,0,0,.25)}
.dots{position:absolute;left:99px;top:399px;display:flex;gap:12px}
.dots span{width:11px;height:11px;border-radius:50%;background:#6fcb95}
.dots span.on{background:#1f6e40}
.hero-art{position:absolute;left:519px;top:39px;width:441px;height:470px;border-radius:10px;background:linear-gradient(160deg,rgba(255,255,255,.14),rgba(255,255,255,.05))}

/* features */
.intro-title{position:absolute;left:0;top:676px;width:1200px;text-align:center;font-size:40px;color:var(--ink)}
.intro-text{position:absolute;left:119px;top:743px;width:962px;text-align:center;font-size:12.5px;line-height:21px;color:var(--muted)}
.feature{position:absolute;width:300px;text-align:center}
.feature-art{margin:0 auto;border-radius:6px}
.feature h3{font-family:"Signika",sans-serif;font-weight:300;font-size:24px;color:var(--ink);margin-top:14px}
.feature p{font-size:12.5px;line-height:20.5px;color:var(--muted);margin-top:8px}

/* testimonials */
.trust{position:absolute;left:0;top:1466px;width:1200px;height:492px;background:var(--mist)}
.trust-title{position:absolute;left:0;top:62px;width:1200px;text-align:center;font-size:38px;color:var(--ink)}
.trust-sub{position:absolute;left:0;top:122px;width:1200px;text-align:center;font-size:12.5px;color:var(--text)}
.quote{position:absolute;top:186px;width:308px}
.quote-box{position:relative;height:158px;background:var(--white);padding:32px 20px 0;text-align:center;font-size:12.5px;line-height:20.5px;color:#666}
.quote-box::after{content:"";position:absolute;left:38px;bottom:-26px;border-left:20px solid transparent;border-top:26px solid var(--white)}
.quote-name{margin:42px 0 0 4px;font-size:17px;color:var(--ink)}
.quote-handle{margin:2px 0 0 2px;font-size:12px;color:#666}

/* call to action */
.cta{position:absolute;left:0;top:1958px;width:1200px;height:119px;background:var(--ink-soft);display:flex;align-items:center;justify-content:center;gap:26px}
.cta-text{font-size:28px;color:var(--white);white-space:nowrap}
.cta-btn{flex:none;width:230px;height:63px;background:var(--green);color:var(--white);font-family:"Signika",sans-serif;font-weight:600;font-size:19px;display:flex;align-items:center;justify-content:center;box-shadow:0 3px 0 #1f6e40}

/* footer */
.footer{position:absolute;left:0;top:2077px;width:1200px;height:400px;background:var(--green);color:var(--white)}
.footer-col{position:absolute;top:45px}
.footer-col h4{font-family:"Signika",sans-serif;font-weight:600;font-size:19px;margin-bottom:14px}
.footer-col li{list-style:none;font-size:12.5px;line-height:25.6px}
.footer-col .contact-note{font-size:12.5px;line-height:21px;width:210px;margin-bottom:8px}
.social li{display:flex;align-items:center;gap:10px;line-height:31px}
.social i{width:11px;height:11px;background:var(--white);border-radius:2px;display:block}
.legal{position:absolute;left:0;top:2477px;width:1200px;height:73px;background:var(--green-dark);color:var(--white);font-size:12.5px;display:flex;align-items:center;justify-content:center;gap:16px}
</style>
</head>
<body>

<header class="topbar">
  <div class="brand">Servanilo</div>
  <nav class="nav">
    <svg class="home" viewBox="0 0 18 16"><path d="M9 1 1 8h2.5v7h4v-5h3v5h4V8H17z" fill="#9a9a9a"/></svg>
    <a>Features</a><a>Pricing</a><a>Add-ons</a><a>Resources</a><a>Login</a>
  </nav>
  <a class="signup">SIGN UP</a>
  <div class="langs"><span style="background:#d9a400"></span><span style="background:#4a5fa0"></span></div>
</header>

<section class="hero">
  <h1 class="hero-title">Cloud Hosting</h1>
  <p class="hero-sub">High performance SSD Linux servers for all of your infrastructure needs.</p>
  <a class="hero-btn">VIEW PLAN &amp; PRICING</a>
  <div class="dots"><span class="on"></span><span></span><span></span></div>
  <div class="hero-art" role="img" aria-label="Illustration of a cloud connected to a phone, desktop monitor, laptop and tablet"></div>
</section>

<h2 class="intro-title heading">Simple. Powerful. Reliable.</h2>
<p class="intro-text">Nemo enim ipsam voluptatem quia voluptas sit aspernatur aut odit aut fugit, sed quia consequuntur magni dolores eos qui ratione voluptatem sequi nesciunt. Neque porro quisquam est, qui dolorem ipsum quia dolor sit amet, consectetur, adipisci velit.</p>

<div class="feature" style="left:102px;top:841px">
  <div class="feature-art" role="img" aria-label="Server racks illustration" style="width:163px;height:124px;background:linear-gradient(#3a3a3a,#555)"></div>
  <h3>Lorem ipsum dolor</h3>
  <p>Neque porro quisquam est, qui dolorem ipsum quia dolor sit amet, consectetur, adipisci velit, sed quia non numquam eius modi tempora</p>
</div>
<div class="feature" style="left:452px;top:841px">
  <div class="feature-art" role="img" aria-label="Image gallery illustration" style="width:160px;height:124px;background:linear-gradient(#f4f4f4 0%,#f4f4f4 55%,#4cae3c 56%)"></div>
  <h3>Lorem ipsum dolor</h3>
  <p>Neque porro quisquam est, qui dolorem ipsum quia dolor sit amet, consectetur, adipisci velit, sed quia non numquam eius modi tempora</p>
</div>
<div class="feature" style="left:804px;top:841px">
  <div class="feature-art" role="img" aria-label="Code editor window illustration" style="width:180px;height:124px;background:linear-gradient(#e0e0e0 0,#e0e0e0 16%,#3a3a3a 16%)"></div>
  <h3>Lorem ipsum dolor</h3>
  <p>Neque porro quisquam est, qui dolorem ipsum quia dolor sit amet, consectetur, adipisci velit, sed quia non numquam eius modi tempora</p>
</div>

<div class="feature" style="left:102px;top:1147px">
  <div class="feature-art" role="img" aria-label="Browser window layout illustration" style="width:146px;height:124px;background:linear-gradient(#c4c4c4 0,#c4c4c4 20%,#6a6a6a 20%)"></div>
  <h3>Lorem ipsum dolor</h3>
  <p>Neque porro quisquam est, qui dolorem ipsum quia dolor sit amet, consectetur, adipisci velit, sed quia non numquam eius modi tempora</p>
</div>
<div class="feature" style="left:452px;top:1147px">
  <div class="feature-art" role="img" aria-label="Laptop with dashboard illustration" style="width:174px;height:124px;background:linear-gradient(90deg,#f0b323 0,#f0b323 55%,#b38fb8 55%,#f1a7c9)"></div>
  <h3>Lorem ipsum dolor</h3>
  <p>Neque porro quisquam est, qui dolorem ipsum quia dolor sit amet, consectetur, adipisci velit, sed quia non numquam eius modi tempora</p>
</div>
<div class="feature" style="left:804px;top:1147px">
  <div class="feature-art" role="img" aria-label="Tablet with profile screen illustration" style="width:94px;height:108px;margin:8px auto 8px;background:linear-gradient(#b9d98a,#9cc56a 70%,#3a3a3a 70%)"></div>
  <h3>Lorem ipsum dolor</h3>
  <p>Neque porro quisquam est, qui dolorem ipsum quia dolor sit amet, consectetur, adipisci velit, sed quia non numquam eius modi tempora</p>
</div>

<section class="trust">
  <h2 class="trust-title heading">Over 350,000 Customers Trust</h2>
  <p class="trust-sub">You don't have to take our word for it.</p>
  <div class="quote" style="left:99px">
    <div class="quote-box">Neque porro quisquam est, qui dolorem ipsum quia dolor sit amet, consectetur, adipisci velit, sed quia non numquam eius modi tempora incidunt ut labore et dolore</div>
    <p class="quote-name">Alan Marsh</p><p class="quote-handle">@amarsh</p>
  </div>
  <div class="quote" style="left:446px">
    <div class="quote-box">Neque porro quisquam est, qui dolorem ipsum quia dolor sit amet, consectetur, adipisci velit, sed quia non numquam eius modi tempora incidunt ut labore et dolore</div>
    <p class="quote-name">Alan Marsh</p><p class="quote-handle">@amarsh</p>
  </div>
  <div class="quote" style="left:793px">
    <div class="quote-box">Neque porro quisquam est, qui dolorem ipsum quia dolor sit amet, consectetur, adipisci velit, sed quia non numquam eius modi tempora incidunt ut labore et dolore</div>
    <p class="quote-name">Alan Marsh</p><p class="quote-handle">@amarsh</p>
  </div>
</section>

<section class="cta">
  <p class="cta-text heading">Get started in the Nimbora Cloud today.</p>
  <a class="cta-btn">CREATE AN ACCOUNT</a>
</section>

<footer class="footer">
  <div class="footer-col" style="left:99px">
    <h4>OVERVIEW</h4>
    <ul><li>Plans &amp; Pricing</li><li>Features</li><li>Backups</li><li>Balancers</li><li>Watchtower</li><li>Managed</li><li>Professional Services</li><li>DeployKits</li><li>Mobile</li><li>CLI</li><li>API</li></ul>
  </div>
  <div class="footer-col" style="left:411px">
    <h4>RESOURCES</h4>
    <ul><li>Getting Started</li><li>Migrating</li><li>Hosting a Website</li><li>Guides &amp; Tutorials</li><li>Standards &amp; Compliance</li><li>Speed Test</li><li>Forum</li><li>Chat</li><li>System Status</li></ul>
  </div>
  <div class="footer-col" style="left:728px">
    <h4>COMPANY</h4>
    <ul><li>About Us</li><li>Employees</li><li>Blog</li><li>Events</li><li>Press</li><li>Case Studies</li><li>Logos</li><li>Careers</li><li>Contact</li></ul>
  </div>
  <div class="footer-col" style="left:933px">
    <h4>CONTACT US</h4>
    <p class="contact-note">Nemo enim ipsam voluptatem quia voluptas sit</p>
    <p class="contact-note">(555-010-4567)</p>
    <ul class="social"><li><i></i>Friendboard</li><li><i></i>Chirper</li><li><i></i>Circleplus</li><li><i></i>Workweb</li></ul>
  </div>
</footer>

<div class="legal"><span>© 2015 servanilo.example</span><span>Terms of Service</span><span>|</span><span>Privacy Policy</span></div>

</body>
</html>
```